Logo and Card design for KRV Home Solutions LLC

I need an edgier logo and business card designs. Current logo attached. I like the colors below. I would like the logo to incorporate a home in the design.
Title = Principal-Acquisitions
Email:KRVHOMESOLUTIONS@fernmail.example
555-214-0937
facebook
IG
2 sided business card with the front being contact info a slogan about selling a home fast. The back incorporating What we do. Buy houses, land, or commercial property as is. We find solutions to make the process of selling simple and fair.

Target Market(s)

Motivated house sellers.

Industry/Entity Type

Business

Contact Information for Business Card

Who we are: We are a Faith based Real Estate Investment Company. We pay cash for homes in any condition and can close quick. Whatever the reason you need to sell fast, we can help. We believe in creating win-win solutions to help you in your time of need. We care! We can help!

Logo Text

KRV Home Solutions LLC

Font styles to use
Sans Serif

Colors
33a6d7
0355a3
85abd2
cee9f5
9d9d9d
b2b2b2
ffffff

Requirements
Must have
• Old logo attached. I want something edgier.
• Company name, phone number, description on the back of what we can do. Pay all cash. Buy in as is condition. No fees,Commisions or closing costs.Close quick. No hassles with solutions to meet your unique situation.
• Call today for an offer within 24 hours.

```html
<!DOCTYPE html>
<html lang="en">
<head>
<meta charset="utf-8">
<title>KRV Home Solutions – Business Card</title>
<link rel="stylesheet" href="https://fonts.googleapis.com/css2?family=Lato:wght@400;700&display=swap">
<style>
  :root {
    --backdrop: #b3b6bd;
    --navy: #1f3a78;
    --navy-deep: #1b3470;
    --name-blue: #1d4f9e;
    --slate: #7d8089;
    --ink: #333333;
    --white: #ffffff;
  }
  * { margin: 0; padding: 0; box-sizing: border-box; }
  html, body {
    width: 1200px; height: 900px; overflow: hidden;
    background: var(--backdrop);
    font-family: "Lato", sans-serif;
  }
  .card {
    position: absolute; top: 306px; height: 271px;
    box-shadow: 2px 3px 5px rgba(0,0,0,0.35);
    overflow: hidden;
  }
  /* Front */
  .card-front { left: 149px; width: 439px; background: var(--white); }
  .corner-mark { position: absolute; left: 0; top: 26px; }
  .person { position: absolute; left: 35px; top: 31px; }
  .person-name { font-size: 17px; font-weight: 700; color: var(--name-blue); line-height: 20px; letter-spacing: 0.2px; }
  .person-title { font-size: 13px; color: var(--ink); line-height: 16px; }
  .brand {
    position: absolute; left: 236px; top: 80px; width: 180px;
    display: flex; align-items: center; gap: 8px;
  }
  .brand-dot { width: 14px; height: 14px; background: var(--slate); flex: none; }
  .brand-name { font-size: 21px; font-weight: 700; color: var(--navy); line-height: 24px; }
  .contact { position: absolute; left: 32px; top: 176px; color: var(--ink); }
  .contact-line { display: flex; align-items: center; gap: 5px; }
  .contact-phone { font-size: 15px; line-height: 18px; }
  .contact-email { font-size: 12.5px; line-height: 17px; }
  .social { position: absolute; left: 360px; top: 182px; display: flex; gap: 6px; }
  .social-dot { width: 23px; height: 23px; border-radius: 50%; background: var(--navy); }
  .front-band {
    position: absolute; left: 0; bottom: 0; width: 100%; height: 45px;
    background: var(--navy); color: var(--white);
    font-size: 13px; font-weight: 700; text-align: center; line-height: 45px;
  }
  /* Back */
  .card-back { left: 608px; width: 441px; background: linear-gradient(135deg, #2a4785 0%, var(--navy-deep) 55%, #1d3672 100%); }
  .back-art { position: absolute; inset: 0 0 42px 0; }
  .services { position: absolute; left: 38px; top: 38px; list-style: none; color: var(--white); font-size: 13px; line-height: 16px; }
  .services li { display: flex; gap: 5px; }
  .services li::before { content: "\2605"; font-size: 9px; }
  .services .lead { font-weight: 700; }
  .services .gap { margin-top: 16px; }
  .back-band {
    position: absolute; left: 0; bottom: 0; width: 100%; height: 42px;
    background: var(--white); color: var(--navy);
    font-size: 15px; font-weight: 700; text-align: center; line-height: 36px;
  }
</style>
</head>
<body>
  <section class="card card-front">
    <svg class="corner-mark" width="30" height="37" viewBox="0 0 30 37">
      <polygon points="0,0 10,0 14,37 0,37" fill="var(--slate)"/>
      <polygon points="12,0 28,0 28,37 16,37" fill="var(--navy)"/>
    </svg>
    <div class="person">
      <div class="person-name">MARCUS HALE</div>
      <div class="person-title">Managing Director</div>
    </div>
    <div class="brand">
      <span class="brand-dot"></span>
      <span class="brand-name">KRV Home Solutions</span>
    </div>
    <div class="contact">
      <div class="contact-line contact-phone">
        <svg width="10" height="9" viewBox="0 0 10 9"><path d="M1 3 Q5 -1 9 3 L8 4 L6.5 3 L6.5 2.3 Q5 1.8 3.5 2.3 L3.5 3 L2 4 Z M2 5 L8 5 L8 8 L2 8 Z" fill="var(--navy)"/></svg>
        <span>555-214-0937</span>
      </div>
      <div class="contact-line contact-email">
        <svg width="9" height="7" viewBox="0 0 9 7"><rect width="9" height="7" fill="var(--navy)"/><path d="M0 0 L4.5 4 L9 0" stroke="#fff" stroke-width="0.8" fill="none"/></svg>
        <span>KRVHOMESOLUTIONS@fernmail.example</span>
      </div>
    </div>
    <div class="social">
      <span class="social-dot"></span>
      <span class="social-dot"></span>
    </div>
    <div class="front-band">CALL TODAY TO GET AN ALL CASH OFFER WITHIN 24 HOURS</div>
  </section>

  <section class="card card-back">
    <div class="back-art" role="img" aria-label="Faint oversized house emblem in the background"></div>
    <ul class="services">
      <li class="lead">Need Cash?&nbsp; Need to sell your house fast?&nbsp; Vacant house?</li>
      <li class="gap">KRV Home Solutions can help with your unique situation.</li>
      <li>We make selling your house easy!</li>
      <li class="gap">We buy houses, land or commercial property as is.</li>
      <li>We pay cash and cover all closing costs.</li>
      <li>We make the repairs so you don't have to.</li>
      <li>Close fast and move on with your life!</li>
      <li class="gap">CALL OR TEXT TODAY!</li>
    </ul>
    <div class="back-band">CALL OR TEXT TODAY TO HEAR OUR CASH OFFER!</div>
  </section>
</body>
</html>
```